Business Card Design

We need a business card designed for our new company. Prefer a black card with white logo & writing.

Contact Information for Business Card

Ted Galloway, address: 7-4812 Fernhollow Road, Abbotsford, BC, V3K 8R2, Office Phone: 604-712-3390, Cell: 604-947-2164, Email: ted@resinworkshub.ca

Colors

Designer to choose only greyscale colors for use in the design.

```html
<!DOCTYPE html>
<html lang="en">
<head>
<meta charset="utf-8">
<title>Resinworks Hub – Business Card</title>
<link rel="stylesheet" href="https://fonts.googleapis.com/css2?family=Poppins:wght@300;400;600;700&display=swap">
<style>
  :root {
    --backdrop: #232323;
    --card: #1c1c1f;
    --ink: #ffffff;
    --ink-soft: #e6e6e6;
    --emboss: #8e8e93;
  }
  * { margin: 0; padding: 0; box-sizing: border-box; }
  html, body {
    width: 1200px; height: 780px; overflow: hidden;
    background: var(--backdrop);
    font-family: "Poppins", sans-serif;
    color: var(--ink);
  }
  .canvas { position: relative; width: 1200px; height: 780px; }

  .card {
    position: absolute;
    background: var(--card);
    box-shadow: 0 18px 40px rgba(0,0,0,.55);
  }

  /* Contact side – portrait */
  .card-front {
    left: 150px; top: 92px; width: 340px; height: 596px;
    padding: 42px 34px 40px;
    display: flex; flex-direction: column;
  }
  .brand {
    align-self: flex-end;
    display: flex; align-items: center; gap: 10px;
    font-weight: 600; font-size: 21px; letter-spacing: .01em;
    color: var(--ink);
  }
  .brand-mark {
    width: 14px; height: 14px; background: var(--ink);
  }
  .contact {
    margin-top: 34px;
    text-align: right;
    font-weight: 300; font-size: 12.5px; line-height: 1.55;
    color: var(--ink-soft);
  }
  .contact .address { margin-bottom: 14px; }
  .contact .lines { margin-bottom: 14px; }
  .contact .line {
    display: flex; justify-content: flex-end; align-items: center; gap: 8px;
  }
  .contact .icon { width: 12px; height: 12px; flex: none; }
  .person { margin-top: auto; }
  .person-name {
    font-weight: 400; font-size: 30px; line-height: 1.1;
  }
  .person-name strong { font-weight: 700; }
  .person-role {
    margin-top: 6px; font-weight: 300; font-size: 14px; color: var(--ink-soft);
  }

  /* Brand side – landscape */
  .card-back {
    left: 560px; top: 230px; width: 560px; height: 320px;
    display: flex; align-items: center; justify-content: center;
  }
  .card-back .brand {
    align-self: center;
    font-size: 40px; gap: 16px;
    color: var(--emboss);
  }
  .card-back .brand-mark { width: 24px; height: 24px; background: var(--emboss); }
</style>
</head>
<body>
<main class="canvas">

  <section class="card card-front" aria-label="Business card, contact side">
    <div class="brand"><span class="brand-mark"></span>Resinworks Hub</div>

    <div class="contact">
      <p class="address">7-4812 Fernhollow Road,<br>Abbotsford, BC, V3K 8R2.</p>
      <div class="lines">
        <p class="line">604-712-3390
          <svg class="icon" viewBox="0 0 24 24" fill="currentColor" aria-hidden="true"><path d="M6.6 10.8a15 15 0 0 0 6.6 6.6l2.2-2.2a1 1 0 0 1 1-.25 11.4 11.4 0 0 0 3.6.57 1 1 0 0 1 1 1V20a1 1 0 0 1-1 1A17 17 0 0 1 3 4a1 1 0 0 1 1-1h3.5a1 1 0 0 1 1 1c0 1.25.2 2.45.57 3.6a1 1 0 0 1-.25 1z"/></svg>
        </p>
        <p class="line">604-947-2164
          <svg class="icon" viewBox="0 0 24 24" fill="none" stroke="currentColor" stroke-width="2" aria-hidden="true"><rect x="6" y="2" width="12" height="20" rx="2"/><line x1="11" y1="18" x2="13" y2="18"/></svg>
        </p>
      </div>
      <p class="line">www.resinworkshub.ca
        <svg class="icon" viewBox="0 0 24 24" fill="none" stroke="currentColor" stroke-width="2" aria-hidden="true"><circle cx="12" cy="12" r="10"/><path d="M2 12h20M12 2a15 15 0 0 1 0 20M12 2a15 15 0 0 0 0 20"/></svg>
      </p>
      <p class="line">ted@resinworkshub.ca
        <svg class="icon" viewBox="0 0 24 24" fill="none" stroke="currentColor" stroke-width="2" aria-hidden="true"><rect x="2" y="5" width="20" height="14" rx="1"/><path d="M2 6l10 7 10-7"/></svg>
      </p>
    </div>

    <div class="person">
      <p class="person-name"><strong>Ted</strong> Galloway</p>
      <p class="person-role">Founder &amp; CEO</p>
    </div>
  </section>

  <section class="card card-back" aria-label="Business card, brand side">
    <div class="brand"><span class="brand-mark"></span>Resinworks Hub</div>
  </section>

</main>
</body>
</html>
```